Sunscreen Package Design Modern SPF 50

Update current package design to a more modern design target women 16-40 Do not make it playful. MESA HAVEN is home to movie stars and high income business people PalmSprings is one of the most desired vacation areas in the world. The sun shines 350 days a year. World class Tennis and Golf tournaments are held every year with the worlds top players attending these tournaments

Target Market(s)

Women

Industry/Entity Type

Skin Protection

Font styles to use
Sans Serif

Requirements
Must have
• The words MESA HAVEN and KORIVELL

```html
<!DOCTYPE html>
<html lang="en">
<head>
<meta charset="utf-8">
<title>Mesa Haven KORIVELL – Sunscreen &amp; Aftersun</title>
<link href="https://fonts.googleapis.com/css2?family=Poppins:wght@400;500;600&display=swap" rel="stylesheet">
<style>
  :root{
    --bg:#e4e4e4;
    --sun-tube:#f1cfa9;
    --sun-mark:#eca05f;
    --sun-pill:#eba862;
    --sun-spf:#e07f4d;
    --sun-text:#5a3f33;
    --after-tube:#a9d5cf;
    --after-mark:#4cbaa8;
    --after-pill:#5ebfab;
    --after-spf:#3aaed1;
    --after-text:#3d3a36;
    --cap:#f6f6f6;
    --cap-edge:#dcdcdc;
  }
  html,body{margin:0;padding:0;overflow:hidden;}
  body{width:1200px;height:912px;background:var(--bg);font-family:"Poppins",sans-serif;position:relative;}
  .tube{position:absolute;top:92px;width:300px;height:729px;}
  .tube--sunscreen{left:279px;}
  .tube--aftersun{left:642px;top:86px;}
  .tube__body{position:absolute;left:0;top:0;width:300px;height:647px;
    clip-path:polygon(0 0,100% 0,80% 100%,20% 100%);}
  .tube--sunscreen .tube__body{background:var(--sun-tube);}
  .tube--aftersun .tube__body{background:var(--after-tube);}
  .tube__cap{position:absolute;left:77px;top:645px;width:146px;height:84px;background:var(--cap);
    border-radius:0 0 12px 12px;box-shadow:inset 0 -6px 0 var(--cap-edge);}
  .tube__cap-notch{position:absolute;left:50px;top:24px;width:46px;height:30px;border:2px solid var(--cap-edge);border-radius:3px;box-sizing:border-box;}
  .label{position:absolute;left:0;width:300px;text-align:center;margin:0;}
  .brand-dot{position:absolute;left:106px;top:75px;width:88px;height:88px;border-radius:50%;}
  .tube--sunscreen .brand-dot{background:var(--sun-mark);}
  .tube--aftersun .brand-dot{background:var(--after-mark);}
  .brand-name{top:186px;font-weight:500;font-size:24px;line-height:30px;letter-spacing:2px;}
  .brand-sub{top:236px;font-weight:500;font-size:15px;line-height:20px;letter-spacing:2px;}
  .tube--sunscreen .brand-name,.tube--sunscreen .brand-sub{color:var(--sun-text);}
  .tube--aftersun .brand-name,.tube--aftersun .brand-sub{color:var(--after-text);}
  .product-pill{position:absolute;left:55px;top:291px;width:186px;height:28px;border-radius:14px;
    font-weight:600;font-size:19px;line-height:28px;letter-spacing:3px;text-align:center;}
  .tube--sunscreen .product-pill{background:var(--sun-pill);color:#fbe3c8;}
  .tube--aftersun .product-pill{background:var(--after-pill);color:#e4f5f1;left:57px;}
  .spf-badge{position:absolute;left:92px;top:358px;width:108px;height:65px;border-radius:5px;}
  .tube--sunscreen .spf-badge{background:var(--sun-spf);color:#fde9da;}
  .tube--aftersun .spf-badge{background:var(--after-spf);color:#e3f6fb;left:97px;}
  .spf-badge__label{position:absolute;left:7px;top:7px;font-size:13px;}
  .spf-badge__value{position:absolute;left:36px;top:0;font-weight:600;font-size:46px;line-height:65px;}
  .claim{font-size:13px;line-height:16px;}
  .claim--top{top:437px;}
  .claim--list{top:496px;font-size:15px;line-height:19px;letter-spacing:.5px;}
  .volume{top:606px;font-size:14px;line-height:18px;}
  .tube--sunscreen .claim,.tube--sunscreen .volume{color:var(--sun-text);}
  .tube--aftersun .claim,.tube--aftersun .volume{color:var(--after-text);}
</style>
</head>
<body>
  <section class="tube tube--sunscreen" aria-label="Sunscreen tube label">
    <div class="tube__body">
      <div class="brand-dot"></div>
      <h1 class="label brand-name">MESA HAVEN</h1>
      <p class="label brand-sub">KORIVELL</p>
      <div class="product-pill">SUNSCREEN</div>
      <div class="spf-badge"><span class="spf-badge__label">SPF</span><span class="spf-badge__value">50</span></div>
      <p class="label claim claim--top">Water Resistant<br>80 minutes</p>
      <p class="label claim claim--list">UVA + UVB<br>PROTECTION<br>BROAD SPECTRUM</p>
      <p class="label volume">3 fl. oz. / 88 ml</p>
    </div>
    <div class="tube__cap"><div class="tube__cap-notch"></div></div>
  </section>

  <section class="tube tube--aftersun" aria-label="Aftersun tube label">
    <div class="tube__body">
      <div class="brand-dot"></div>
      <h2 class="label brand-name">MESA HAVEN</h2>
      <p class="label brand-sub">KORIVELL</p>
      <div class="product-pill">AFTERSUN</div>
      <div class="spf-badge"><span class="spf-badge__label">SPF</span><span class="spf-badge__value">50</span></div>
      <p class="label claim claim--top">Hydrate your skin with<br>These Essential ingredients</p>
      <p class="label claim claim--list">HYALURONATE ACID<br>CUCUMBER / ALOE<br>JOJOBA / SUNFLOWER</p>
      <p class="label volume">3 fl. oz. / 88 ml</p>
    </div>
    <div class="tube__cap"><div class="tube__cap-notch"></div></div>
  </section>
</body>
</html>
```